Brenlow Estates Website and Logo Design

We need a new logo and website designed for 'Brenlow Estates Ltd', which is a well established Guernsey property holding company founded in 1934.

The company does not currently have a website. The new website should be similar in style and layout to https://www.quorvanhall.example/.

Target Market(s)

Industry, Media, Tenants

Industry/Entity Type

Property Management

Logo Text

BEL OR Brenlow Estates Ltd OR BE

Coding

Coded - Design and coding required

Number of Pages Required

4 page

Font styles to use
Other font styles liked:
• Helvetica

Requirements
Must have
• The logo laying over the picture (like https://www.quorvanhall.example/).
• Big pictures on homepage (like https://www.quorvanhall.example/)

```html
<!DOCTYPE html>
<html lang="en">
<head>
<meta charset="utf-8">
<title>Brenlow Estates</title>
<link href="https://fonts.googleapis.com/css2?family=Nunito+Sans:wght@300;400;600;700;800&display=swap" rel="stylesheet">
<style>
:root{
  --blue:#1a5ea8;
  --orange:#d9730f;
  --ink:#333333;
  --grey:#7a7a7a;
  --light:#f2f2f2;
  --line:#d8d8d8;
  --white:#ffffff;
}
*{margin:0;padding:0;box-sizing:border-box}
html,body{width:1200px;height:2436px;overflow:hidden}
body{position:relative;background:var(--white);font-family:"Nunito Sans",Helvetica,Arial,sans-serif;color:var(--ink)}
.abs{position:absolute}

/* Hero */
.hero{left:0;top:0;width:1200px;height:638px;background:linear-gradient(180deg,#7e98b8 0%,#6f8bb0 20%,#3f5f86 38%,#3b5a80 60%,#34506f 80%,#4a5560 100%)}
.brand{left:143px;top:66px;color:var(--white);font-weight:700;font-size:30px;letter-spacing:-.3px;line-height:40px}
.brand-dot{left:236px;top:18px;width:22px;height:22px;border-radius:50%;background:var(--white)}
.main-nav{top:58px;left:0;width:1200px;height:36px}
.main-nav a{position:absolute;top:0;height:36px;line-height:36px;color:var(--white);text-decoration:none;font-size:17px;transform:translateX(-50%)}
.main-nav a.active{border:2px solid var(--white);width:90px;text-align:center;line-height:32px}
.hero-title{left:0;width:1200px;text-align:center;color:var(--white);text-transform:uppercase}
.hero-title.sub{top:260px;font-size:33px;font-weight:600}
.hero-title.main{top:295px;font-size:43px;font-weight:700}
.btn-outline-white{left:529px;top:367px;width:95px;height:37px;border:2px solid var(--white);color:var(--white);font-size:13px;font-weight:600;text-align:center;line-height:33px}
.dots{top:597px;left:557px;display:flex;gap:10px}
.dots span{width:14px;height:14px;border-radius:50%;background:var(--white)}
.dots span.off{background:transparent;border:2px solid var(--white)}

/* About */
.section-title{left:0;width:1200px;text-align:center;color:var(--blue);font-size:31px;font-weight:400;top:683px}
.intro{left:200px;top:741px;width:800px;text-align:center;color:var(--grey);font-size:15px;line-height:27.6px}
.btn-solid{left:516px;top:875px;width:138px;height:38px;background:var(--blue);color:var(--white);font-size:14px;font-weight:600;text-align:center;line-height:38px}

.card-photo{top:973px;width:441px;height:217px}
.photo-castle{left:140px;background:linear-gradient(180deg,#3d4656 0%,#4a4f5a 45%,#7a5a2f 60%,#303640 100%)}
.photo-harbour{left:606px;background:linear-gradient(180deg,#b7c9dc 0%,#7a8c74 28%,#2f7a88 45%,#2c6e7a 100%)}
.card-title{top:1202px;width:441px;text-align:center;font-size:27px;font-weight:400;color:var(--ink)}
.card-text{top:1249px;width:390px;text-align:center;font-size:13.5px;line-height:24px;color:var(--grey)}
.btn-outline-blue{top:1333px;width:123px;height:33px;border:2px solid var(--blue);color:var(--blue);font-size:12.5px;font-weight:600;text-align:center;line-height:29px}

/* Band */
.band{left:0;top:1447px;width:1200px;height:374px;background:linear-gradient(180deg,#2c6bb8 0%,#1a5aa8 60%,#134f9c 100%)}
.band-box{top:1492px;width:457px;height:280px;border:1.5px solid rgba(255,255,255,.75)}
.band-icon{top:1528px;width:62px;height:62px;border-radius:50%;border:2.5px solid rgba(255,255,255,.9)}
.band-title{top:1532px;color:var(--white);font-size:29px;font-weight:400}
.band-text{top:1582px;width:330px;color:var(--white);font-size:14px;line-height:25px;font-weight:300;white-space:nowrap}
.read-more{top:1690px;color:var(--white);font-size:13.5px;font-weight:700;padding-bottom:6px;border-bottom:2px solid var(--white)}

/* Lists */
.list-title{top:1872px;font-size:28px;font-weight:400}
.list-title.blogs{left:141px;color:var(--orange)}
.list-title.news{left:643px;color:var(--ink)}
.thumb{width:143px;height:122px}
.item-title{color:var(--blue);font-size:16px;font-weight:600}
.item-text{color:var(--grey);font-size:13px;line-height:20px;width:280px}
.item-more{color:var(--orange);font-size:13.5px;font-weight:600}
.news-meta{color:var(--ink);font-size:13px}
.divider{left:645px;width:402px;height:1px;background:var(--line)}
.news-link{left:645px;color:var(--blue);font-size:17px}
.news-sub{left:645px;color:var(--grey);font-size:14.5px}

/* Footer */
.footer{left:0;top:2296px;width:1200px;height:140px;background:var(--light)}
.foot-nav{top:2332px;left:0;width:1200px;height:22px}
.foot-nav a{position:absolute;top:0;color:var(--ink);text-decoration:none;font-size:15px}
.copyright{left:145px;top:2366px;font-size:12.5px;color:var(--ink)}
.social{top:2330px;width:28px;height:28px;border-radius:50%;background:var(--white);border:1px solid #e2e2e2}
</style>
</head>
<body>

<header>
  <div class="abs hero" role="img" aria-label="Photograph of a sheltered Guernsey bay with small rowing boats and rocky islets"></div>
  <div class="abs brand-dot"></div>
  <div class="abs brand">Brenlow Estates</div>
  <nav class="abs main-nav">
    <a href="#" class="active" style="left:456px">Home</a>
    <a href="#" style="left:561px">About Us</a>
    <a href="#" style="left:656px">Why</a>
    <a href="#" style="left:749px">Services</a>
    <a href="#" style="left:843px">News</a>
    <a href="#" style="left:929px">Blogs</a>
    <a href="#" style="left:1024px">Contact</a>
  </nav>
  <h2 class="abs hero-title sub">Morbi porta libero ullamcorp</h2>
  <h1 class="abs hero-title main">Nonummy nibh ligula pulvinar</h1>
  <div class="abs btn-outline-white">LEARN MORE</div>
  <div class="abs dots"><span class="off"></span><span></span><span></span><span></span></div>
</header>

<main>
  <section class="about">
    <h2 class="abs section-title">Brenlow Estates Limited</h2>
    <p class="abs intro">Brenlow Estates Limited (BEL) is a family-owned Guernsey property holding company. It purchases properties that are considered to have potential for development either through refurbishment or by obtaining planning permission to change its classification from, for example, industrial premises to offices or retail outlets, or by the marriage value of buying an adjacent property to one already owned by BEL.</p>
    <div class="abs btn-solid">LEARN MORE</div>

    <div class="abs card-photo photo-castle" role="img" aria-label="Photograph of a lit island castle at dusk"></div>
    <h3 class="abs card-title" style="left:140px">Why Guernsey?</h3>
    <p class="abs card-text" style="left:165px">The Bailiwick of Guernsey is a British Crown dependency in the English Channel. The benefit of establishing a company in Guernsey is the island's low tax jurisdiction since</p>
    <div class="abs btn-outline-blue" style="left:299px">LEARN MORE</div>

    <div class="abs card-photo photo-harbour" role="img" aria-label="Photograph of a harbour with moored boats and a headland"></div>
    <h3 class="abs card-title" style="left:606px">Yesterday</h3>
    <p class="abs card-text" style="left:631px">BEL was founded in 1934 by Harold Brenlow to manage both<br>his own extensive investments and his<br>property portfolio in Guernsey</p>
    <div class="abs btn-outline-blue" style="left:766px">LEARN MORE</div>
  </section>

  <section class="values">
    <div class="abs band" role="img" aria-label="Blue-tinted photograph of a harbour town waterfront"></div>

    <div class="abs band-box" style="left:138px"></div>
    <div class="abs band-icon" style="left:182px" role="img" aria-label="Icon for today"></div>
    <h3 class="abs band-title" style="left:265px">Today</h3>
    <p class="abs band-text" style="left:267px">The Brenlow family has steadily built on the<br>foundations set out by the founder and each<br>generation develops and manages the<br>company appropriate to the era</p>
    <div class="abs read-more" style="left:267px">READ MORE</div>

    <div class="abs band-box" style="left:599px"></div>
    <div class="abs band-icon" style="left:648px" role="img" aria-label="Icon for tomorrow"></div>
    <h3 class="abs band-title" style="left:718px">Tomorrow</h3>
    <p class="abs band-text" style="left:725px">In keeping with its past project development<br>philosophy, its intrinsic understanding of the<br>local property market and the successful<br>management succession</p>
    <div class="abs read-more" style="left:727px">READ MORE</div>
  </section>

  <section class="blogs">
    <h2 class="abs list-title blogs">Latest Blogs</h2>

    <div class="abs thumb" style="left:141px;top:1929px;background:linear-gradient(180deg,#9fb8cf 0%,#c9b79a 40%,#3e6f95 70%,#2b5b82 100%)" role="img" aria-label="Photograph of a marina below a hillside town"></div>
    <h3 class="abs item-title" style="left:307px;top:1926px">Morbi porta libero</h3>
    <p class="abs item-text" style="left:307px;top:1954px">pulvinar metus eget consectetuer augue nisi quis lacus Ut ac mi quis lacus mollis aliquam Curabitur iaculis tempus eros</p>
    <div class="abs item-more" style="left:309px;top:2032px">READ MORE</div>

    <div class="abs thumb" style="left:141px;top:2092px;background:linear-gradient(180deg,#c8d2dc 0%,#8c8478 45%,#5a6470 70%,#3c5a78 100%)" role="img" aria-label="Photograph of a city skyline across the water with a ferry"></div>
    <h3 class="abs item-title" style="left:305px;top:2088px">Morbi porta libero id ullamcorper</h3>
    <p class="abs item-text" style="left:305px;top:2116px">pulvinar metus eget consectetuer augue nisi quis lacus Ut ac mi quis lacus mollis aliquam Curabitur iaculis tempus eros</p>
    <div class="abs item-more" style="left:305px;top:2195px">READ MORE</div>
  </section>

  <section class="news">
    <h2 class="abs list-title news">Recent News</h2>

    <div class="abs thumb" style="left:645px;top:1929px;width:167px;background:linear-gradient(180deg,#2a3f78 0%,#3b3f6a 45%,#a0622a 65%,#2a2a3a 100%)" role="img" aria-label="Photograph of a harbour town lit at night"></div>
    <h3 class="abs item-title" style="left:827px;top:1926px;font-weight:400">News Tittle here</h3>
    <p class="abs item-text" style="left:827px;top:1954px;width:220px">pulvinar metus eget consectetuer augue nisi quis lacus Ut ac mi quis lacus mollis aliquam Curabitur</p>
    <div class="abs news-meta" style="left:827px;top:2022px">25 Nov 2016 &nbsp;| &nbsp;READ MORE</div>

    <div class="abs divider" style="top:2075px"></div>
    <div class="abs news-link" style="top:2084px">Aulvinar metus eget</div>
    <div class="abs news-sub" style="top:2108px">consectetuer augue nisi quis lacus Ut ac mi quis lacus</div>

    <div class="abs divider" style="top:2147px"></div>
    <div class="abs news-link" style="top:2162px">Etiam est nunc venenatis</div>
    <div class="abs news-sub" style="top:2186px">Cum sociis natoque penatibus et magnis dis parturient</div>
  </section>
</main>

<footer>
  <div class="abs footer"></div>
  <nav class="abs foot-nav">
    <a href="#" style="left:145px">Home</a>
    <a href="#" style="left:226px">About Us</a>
    <a href="#" style="left:330px">Why</a>
    <a href="#" style="left:398px">Services</a>
    <a href="#" style="left:494px">News</a>
    <a href="#" style="left:572px">Blogs</a>
    <a href="#" style="left:648px">Contact</a>
  </nav>
  <div class="abs copyright">© 2016 Company Name &nbsp;All right reserved &nbsp;Term of Use</div>
  <div class="abs social" style="left:903px" aria-label="Social link"></div>
  <div class="abs social" style="left:943px" aria-label="Social link"></div>
  <div class="abs social" style="left:984px" aria-label="Social link"></div>
  <div class="abs social" style="left:1024px" aria-label="Social link"></div>
</footer>

</body>
</html>
```